The Plate Compass

Cutting Through the Noise to What Actually Works.

Nutrition book

Target Market(s)

People looking to be or get healthy and eat right.

```html
<!DOCTYPE html>
<html lang="en">
<head>
<meta charset="utf-8">
<title>The Plate Compass – Book Cover</title>
<link href="https://fonts.googleapis.com/css2?family=Anton&family=Work+Sans:wght@500;700&display=swap" rel="stylesheet">
<style>
  :root {
    --paper: #efefef;
    --ink: #000000;
    --forest: #0e3319;
    --gold: #bf912e;
    --cream-line: #e2d8bf;
    --food-warm: #d8c2a4;
    --food-berry: #a9566a;
    --food-nut: #d9b98e;
  }
  * { margin: 0; padding: 0; box-sizing: border-box; }
  html, body { width: 927px; height: 1200px; overflow: hidden; background: var(--paper); }
  .cover {
    position: relative;
    width: 927px;
    height: 1200px;
    overflow: hidden;
    background: var(--paper);
    font-family: "Work Sans", sans-serif;
  }
  .cover__backdrop {
    position: absolute;
    inset: 0;
    background:
      radial-gradient(ellipse 260px 320px at 860px 200px, rgba(216,120,110,0.35), transparent 70%),
      radial-gradient(ellipse 300px 260px at 650px 500px, rgba(160,180,120,0.35), transparent 70%),
      radial-gradient(ellipse 220px 300px at 840px 720px, rgba(169,86,106,0.30), transparent 70%),
      radial-gradient(ellipse 380px 380px at 820px 1050px, rgba(217,185,142,0.55), transparent 70%),
      linear-gradient(90deg, var(--paper) 0%, var(--paper) 35%, rgba(220,205,185,0.6) 100%);
  }
  .title {
    position: absolute;
    left: 0;
    width: 100%;
    text-align: center;
    font-family: "Anton", sans-serif;
    line-height: 1;
    text-transform: uppercase;
  }
  .title--the { top: 22px; font-size: 128px; color: var(--ink); transform: scaleX(1.15); }
  .title--plate { top: 150px; font-size: 128px; color: var(--forest); transform: scaleX(1.15); }
  .title--compass { top: 268px; font-size: 148px; color: var(--gold); transform: scaleX(1.12); }
  .tagline {
    position: absolute;
    top: 432px;
    left: 0;
    width: 100%;
    text-align: center;
    font-size: 28px;
    font-weight: 500;
    line-height: 41px;
    letter-spacing: 1.5px;
    color: var(--forest);
  }
  .plate-glow {
    position: absolute;
    left: 138px; top: 501px;
    width: 640px; height: 640px;
    border-radius: 50%;
    background: radial-gradient(circle, rgba(214,190,120,0.45) 40%, rgba(239,239,239,0) 70%);
  }
  .plate-wheel {
    position: absolute;
    left: 178px; top: 541px;
    width: 560px; height: 560px;
  }
  .segment-label {
    position: absolute;
    font-size: 21px;
    font-weight: 500;
    letter-spacing: 1px;
    color: var(--forest);
    white-space: nowrap;
  }
  .segment-label--supplements { left: 113px; top: 562px; }
  .segment-label--calories { left: 693px; top: 562px; }
  .segment-label--noise { left: 100px; top: 800px; }
  .segment-label--protein { left: 748px; top: 800px; }
  .segment-label--timing { left: 127px; top: 1041px; }
  .segment-label--quality { left: 673px; top: 1041px; }
  .author {
    position: absolute;
    top: 1128px;
    left: 0;
    width: 100%;
    text-align: center;
    font-size: 37px;
    font-weight: 700;
    letter-spacing: 3px;
    color: var(--ink);
  }
</style>
</head>
<body>
<main class="cover">
  <div class="cover__backdrop" role="img" aria-label="Softly faded photo of fruit, broccoli, berries and almonds"></div>

  <h1>
    <span class="title title--the">The</span>
    <span class="title title--plate">Plate</span>
    <span class="title title--compass">Compass</span>
  </h1>

  <p class="tagline">Cutting Through the Noise to<br>What Actually Works.</p>

  <div class="plate-glow"></div>
  <svg class="plate-wheel" viewBox="0 0 560 560" role="img" aria-label="Circular wheel of food photos: supplements, junk food, protein foods, a food lab, a meal with a clock, a smiling listener with headphones, and mixed foods in the centre">
    <g stroke="var(--cream-line)" stroke-width="7" stroke-linejoin="round">
      <path d="M280 280 L280 15 A265 265 0 0 1 509.5 147.5 Z" fill="#b98a5c"/>
      <path d="M280 280 L509.5 147.5 A265 265 0 0 1 509.5 412.5 Z" fill="#b25a4c"/>
      <path d="M280 280 L509.5 412.5 A265 265 0 0 1 280 545 Z" fill="#7b6d55"/>
      <path d="M280 280 L280 545 A265 265 0 0 1 50.5 412.5 Z" fill="#7f9052"/>
      <path d="M280 280 L50.5 412.5 A265 265 0 0 1 50.5 147.5 Z" fill="#9a6a48"/>
      <path d="M280 280 L50.5 147.5 A265 265 0 0 1 280 15 Z" fill="#e3dfd7"/>
      <circle cx="280" cy="280" r="124" fill="#c7a37c" stroke-width="9"/>
    </g>
  </svg>

  <span class="segment-label segment-label--supplements">Supplements</span>
  <span class="segment-label segment-label--calories">Calories</span>
  <span class="segment-label segment-label--noise">Noise</span>
  <span class="segment-label segment-label--protein">Protein</span>
  <span class="segment-label segment-label--timing">Meal Timing</span>
  <span class="segment-label segment-label--quality">Food Quality</span>

  <p class="author">CLARA J. WHITFIELD</p>
</main>
</body>
</html>
```